Business Card Design for Occupational Medicine Start Up Company

We need to design a professional business card. We are a healthcare company providing occupational medicine services to blue collar industries. We are professional, efficient and high quality service providers.

Target Market(s)

Blue Collar Industry: Shipbuilding, Ports, Trucking Companies; The Executives and Safety Officers for these companies

Industry/Entity Type

Healthcare

Contact Information for Business Card

Logo, Name, Title, Email, Phone

Other font styles liked:
• Please match our Brand Guide

Requirements
Must have
• Our Company Colors and Logo

```html
<!DOCTYPE html>
<html lang="en">
<head>
<meta charset="utf-8">
<title>Crewline Clinics – Business Card</title>
<link href="https://fonts.googleapis.com/css2?family=Montserrat:wght@400;500;600;700&display=swap" rel="stylesheet">
<style>
  :root {
    --stage: #232323;
    --navy: #2f3175;
    --navy-deep: #2b2c6e;
    --periwinkle: #7a7ae0;
    --sky: #2e9fd9;
    --amber: #e9a83a;
    --paper: #f4f4f2;
    --white: #ffffff;
  }
  * { box-sizing: border-box; margin: 0; padding: 0; }
  html, body { width: 1200px; height: 1200px; overflow: hidden; }
  body {
    background: var(--stage);
    font-family: "Montserrat", sans-serif;
    position: relative;
  }
  .card {
    position: absolute;
    width: 594px;
    height: 349px;
    border-radius: 22px;
    overflow: hidden;
  }
  /* Back side */
  .card-back {
    left: 298px; top: 198px;
    background: var(--navy);
  }
  .back-brand {
    position: absolute;
    left: 0; right: 0; top: 128px;
    display: flex; align-items: center; justify-content: center; gap: 14px;
  }
  .back-brand .mark {
    width: 34px; height: 34px; border-radius: 50%;
    background: var(--periwinkle);
  }
  .back-brand .name {
    color: var(--periwinkle);
    font-weight: 700;
    font-size: 34px;
    letter-spacing: 1px;
  }
  .back-url {
    position: absolute;
    left: 0; right: 0; top: 300px;
    text-align: center;
    font-size: 16px;
    letter-spacing: 1.2px;
    color: var(--white);
  }
  .back-url .accent-sky { color: var(--sky); }
  .back-url .accent-amber { color: var(--amber); }

  /* Front side */
  .card-front {
    left: 292px; top: 636px;
    background: var(--paper);
    color: var(--navy);
  }
  .front-brand {
    position: absolute;
    left: 34px; top: 52px;
    display: flex; align-items: center; gap: 16px;
  }
  .front-brand .mark {
    width: 70px; height: 70px; border-radius: 50%;
    background: var(--navy);
  }
  .front-brand .name {
    color: var(--navy);
    font-weight: 700;
    font-size: 32px;
    letter-spacing: 0.5px;
  }
  .person {
    position: absolute;
    left: 31px; top: 193px;
  }
  .person-name {
    color: var(--sky);
    font-weight: 600;
    font-size: 25px;
    letter-spacing: 0.5px;
    line-height: 1;
  }
  .person-title {
    font-size: 16px;
    margin-top: 6px;
  }
  .address {
    position: absolute;
    left: 31px; top: 261px;
    font-size: 16px;
    line-height: 21px;
  }
  .contacts {
    position: absolute;
    left: 333px; top: 190px;
    list-style: none;
    font-size: 16px;
    line-height: 21.5px;
  }
  .contacts li { display: flex; align-items: center; gap: 12px; }
  .contacts svg { width: 15px; height: 15px; flex: none; }
  .bottom-band {
    position: absolute;
    left: 0; bottom: 0;
    width: 594px; height: 43px;
  }
  .specialty {
    position: absolute;
    left: 290px; right: 0; bottom: 10px;
    text-align: center;
    color: var(--white);
    font-size: 16px;
    letter-spacing: 0.3px;
  }
</style>
</head>
<body>

  <section class="card card-back" aria-label="Card back">
    <div class="back-brand">
      <span class="mark"></span>
      <span class="name">CREWLINE CLINICS</span>
    </div>
    <p class="back-url">www.<span class="accent-sky">crewline</span><span class="accent-amber">clinics</span>.com</p>
  </section>

  <section class="card card-front" aria-label="Card front">
    <div class="front-brand">
      <span class="mark"></span>
      <span class="name">CREWLINE CLINICS</span>
    </div>

    <div class="person">
      <p class="person-name">DANIEL REYES</p>
      <p class="person-title">Senior Doctor</p>
    </div>

    <p class="address">123 Main Road, Suite 345<br>East North, State 12345</p>

    <ul class="contacts">
      <li>
        <svg viewBox="0 0 16 16" aria-hidden="true"><path fill="#2e9fd9" d="M2 6c0-2 3-3.5 6-3.5S14 4 14 6v1h-3V5.5H5V7H2zM4 8h8l1.5 5h-11z"/></svg>
        123-456-7890
      </li>
      <li>
        <svg viewBox="0 0 16 16" aria-hidden="true"><rect x="1" y="3" width="14" height="10" fill="#2f3175"/><path d="M1.5 3.5L8 9l6.5-5.5" stroke="#f4f4f2" stroke-width="1.4" fill="none"/></svg>
        hello@crewline.com
      </li>
      <li>
        <svg viewBox="0 0 16 16" aria-hidden="true"><circle cx="8" cy="8" r="6.5" fill="#e9a83a"/><path d="M1.5 8h13M8 1.5c-3 3.5-3 9.5 0 13M8 1.5c3 3.5 3 9.5 0 13" stroke="#f4f4f2" stroke-width="0.9" fill="none"/></svg>
        www.crewline.com
      </li>
    </ul>

    <svg class="bottom-band" viewBox="0 0 594 43" aria-hidden="true">
      <rect x="0" y="19" width="282" height="5" fill="#2e9fd9"/>
      <rect x="0" y="27" width="276" height="5" fill="#2f3175"/>
      <rect x="0" y="36" width="270" height="7" fill="#e9a83a"/>
      <path d="M300 0H594V43H272L292 6Q295 0 300 0Z" fill="#2f3175"/>
    </svg>
    <p class="specialty">Occupational Medicine</p>
  </section>

</body>
</html>
```